Veltrane Group Business Card Design

The CEO is looking for a new trendy look for his business card.
You can stay with current branding or come up with something new/creative. It can be 3D, including Medical Office buildings. You can use our logo in a variety of colors. Please include name, title, company name, company website, email address, cell number

Target Market(s)

Real Estate Development and Construction

Industry/Entity Type

Health care real estate

Contact Information for Business Card

Rohesh Kamdar, CEO M-604.781.2249 E-roheshkamdar@veltrane.com Address:4180 Lindqvist Ave, Tampa, FL 33482 www.veltrane.com

Font styles to use
Other font styles liked:
• Be creative

Requirements
Must have
• Creative, trendy look
Nice to have
• Please go to our website to get a feel- www. veltrane.com
Should not have
• small fonts

```html
<!DOCTYPE html>
<html lang="en">
<head>
<meta charset="utf-8">
<title>Veltrane Group Business Card</title>
<link href="https://fonts.googleapis.com/css2?family=Montserrat:wght@400;500;700;800&display=swap" rel="stylesheet">
<style>
  :root {
    --navy: #1f3157;
    --navy-deep: #16233f;
    --navy-soft: #2c4170;
    --white: #ffffff;
    --stage: #efece6;
  }
  * { box-sizing: border-box; margin: 0; padding: 0; }
  html, body { width: 1200px; height: 900px; overflow: hidden; }
  body {
    background: var(--stage);
    font-family: "Montserrat", sans-serif;
    position: relative;
  }
  .card {
    position: absolute;
    left: 320px;
    width: 560px;
    height: 320px;
    overflow: hidden;
    background: var(--navy);
    box-shadow: 0 10px 30px rgba(0,0,0,0.18);
  }
  .card--front { top: 90px; }
  .card--back { top: 490px; }
  .card__photo {
    position: absolute;
    inset: 0;
    background:
      linear-gradient(160deg, rgba(44,65,112,0.55) 0%, rgba(22,35,63,0.2) 55%, rgba(22,35,63,0.7) 100%),
      linear-gradient(90deg, var(--navy-soft) 0%, var(--navy) 50%, var(--navy-deep) 100%);
  }
  /* Front */
  .front__band {
    position: absolute;
    left: 0; top: 0; bottom: 0;
    width: 110px;
    background: var(--white);
    display: flex;
    align-items: center;
    justify-content: center;
  }
  .front__url {
    transform: rotate(-90deg);
    white-space: nowrap;
    color: var(--navy);
    font-weight: 700;
    font-size: 19px;
    letter-spacing: 2px;
    padding-bottom: 6px;
    border-bottom: 3px solid var(--navy);
  }
  .front__brand {
    position: absolute;
    left: 110px; right: 0; top: 0; bottom: 0;
    display: flex;
    align-items: center;
    justify-content: center;
  }
  .brand-name {
    font-weight: 800;
    font-size: 42px;
    color: var(--white);
    letter-spacing: -0.5px;
    white-space: nowrap;
  }
  /* Back */
  .back__band {
    position: absolute;
    right: 0; top: 0; bottom: 0;
    width: 120px;
    background: var(--white);
    display: flex;
    align-items: center;
    justify-content: center;
  }
  .back__band .brand-name {
    color: var(--navy);
    font-size: 30px;
    transform: rotate(90deg);
  }
  .back__content {
    position: absolute;
    left: 34px; top: 34px;
    color: var(--white);
  }
  .identity {
    display: flex;
    align-items: stretch;
    gap: 12px;
    margin-bottom: 30px;
  }
  .identity__mark {
    width: 22px;
    background: var(--white);
  }
  .identity__name {
    font-weight: 800;
    font-size: 24px;
    letter-spacing: 0.5px;
    line-height: 1.15;
  }
  .identity__title {
    font-weight: 500;
    font-size: 20px;
    line-height: 1.2;
  }
  .contacts { list-style: none; }
  .contact {
    display: flex;
    align-items: center;
    gap: 12px;
    font-size: 15px;
    font-weight: 400;
    margin-bottom: 11px;
    line-height: 1.2;
  }
  .contact__icon {
    flex: 0 0 24px;
    width: 24px;
    height: 24px;
  }
</style>
</head>
<body>

<section class="card card--front" aria-label="Business card front">
  <div class="card__photo" role="img" aria-label="Navy-tinted photo of a medical office building with palm trees"></div>
  <div class="front__band">
    <span class="front__url">WWW.VELTRANE.COM</span>
  </div>
  <div class="front__brand">
    <span class="brand-name">Veltrane Group</span>
  </div>
</section>

<section class="card card--back" aria-label="Business card back">
  <div class="card__photo" role="img" aria-label="Navy-tinted photo of a medical office building"></div>
  <div class="back__content">
    <div class="identity">
      <div class="identity__mark"></div>
      <div>
        <p class="identity__name">ROHESH KAMDAR</p>
        <p class="identity__title">CEO</p>
      </div>
    </div>
    <ul class="contacts">
      <li class="contact">
        <svg class="contact__icon" viewBox="0 0 24 24"><circle cx="12" cy="12" r="12" fill="#fff"/><path d="M8.5 6.5l2 .2.8 2.6-1.3 1a7 7 0 0 0 3.7 3.7l1-1.3 2.6.8.2 2c-.3.7-1 1.1-1.8 1-4.6-.5-8.2-4.1-8.7-8.7-.1-.8.3-1.5 1.5-1.3z" fill="#1f3157"/></svg>
        <span>604.781.2249</span>
      </li>
      <li class="contact">
        <svg class="contact__icon" viewBox="0 0 24 24"><circle cx="12" cy="12" r="12" fill="#fff"/><rect x="6" y="8" width="12" height="8.5" rx="1" fill="#1f3157"/><path d="M6.5 8.5l5.5 4.2 5.5-4.2" stroke="#fff" stroke-width="1.2" fill="none"/></svg>
        <span>roheshkamdar@veltrane.com</span>
      </li>
      <li class="contact">
        <svg class="contact__icon" viewBox="0 0 24 24"><circle cx="12" cy="12" r="12" fill="#fff"/><path d="M12 5.5a4.3 4.3 0 0 0-4.3 4.3c0 3.2 4.3 8.2 4.3 8.2s4.3-5 4.3-8.2A4.3 4.3 0 0 0 12 5.5z" fill="#1f3157"/><circle cx="12" cy="9.8" r="1.6" fill="#fff"/></svg>
        <span>4180 Lindqvist Ave, Tampa,<br>FL 33482</span>
      </li>
      <li class="contact">
        <svg class="contact__icon" viewBox="0 0 24 24"><circle cx="12" cy="12" r="12" fill="#fff"/><g stroke="#1f3157" stroke-width="1.2" fill="none"><circle cx="12" cy="12" r="6"/><ellipse cx="12" cy="12" rx="2.6" ry="6"/><path d="M6 12h12M7 9h10M7 15h10"/></g></svg>
        <span>www.veltrane.com</span>
      </li>
    </ul>
  </div>
  <div class="back__band">
    <span class="brand-name">Veltrane Group</span>
  </div>
</section>

</body>
</html>
```